Website for IT consulting Company

I need a website upgrade, the existing site content is ok, I would also like to add a testimonial page, the site should be something that is easy for us to update content. You use the content from www.kelvanbrook.com as an example. I will also post update logo and artwork. I also need a contact form with some type of validation or captcha.

I added Coded to the Project

Please omit Address maps

Target Market(s)

small business, service oriented companies. We provide IT Consulting, support and mangement

Industry/Entity Type

Information Technology

Coding

Number of Pages Required

1 page

Font styles to use
Serif
Sans Serif

Requirements
Must have
• Contain logo attached, and content from existing web site www.kelvanbrook.com.
• Also need to update content easily, and be movable to different platforms.
• There is a catch phrase
• "Let us worry about your technology…” “ so you don’t have to!”
• Should be included.
Nice to have
• Testimonial page, Project page where we can post new and past projects and pictures
Should not have
• none

```html
<!DOCTYPE html>
<html lang="en">
<head>
<meta charset="utf-8">
<title>Kelvanbrook Development Group</title>
<link rel="stylesheet" href="https://fonts.googleapis.com/css2?family=Exo+2:ital,wght@0,700;0,800;1,700;1,800&family=Arimo:ital,wght@0,400;0,700;1,400;1,700&family=Tinos&display=swap">
<style>
:root{
  --blue:#1a8fd6;
  --blue-dark:#0d6fb1;
  --blue-light:#3aa6e6;
  --ink:#1c1c1c;
  --text:#2b2b2b;
  --grey-bg:#e6e6e6;
  --grey-panel:#8a8a8a;
  --top-bar:#2b2b2b;
  --footer:#2a2d33;
  --white:#ffffff;
}
*{box-sizing:border-box;margin:0;padding:0}
html,body{width:1200px;height:2835px;overflow:hidden;background:var(--white)}
body{position:relative;font-family:"Arimo",Arial,sans-serif;color:var(--text)}
.section{position:absolute;left:0;width:1200px}
.heading{font-family:"Exo 2",sans-serif;font-style:italic;font-weight:800;text-transform:uppercase;color:var(--ink)}
.heading span{color:var(--blue)}

/* top bar */
.top-bar{top:0;height:34px;background:var(--top-bar)}
.social-top{position:absolute;right:26px;top:4px;display:flex;gap:8px}
.social-top i{display:block;width:26px;height:26px;background:#8d8d8d}
/* header */
.site-header{top:34px;height:91px;background:var(--white)}
.brand{position:absolute;left:80px;top:20px;display:flex;align-items:center;gap:12px}
.brand-mark{width:46px;height:46px;background:var(--blue)}
.brand-name{font-family:"Exo 2",sans-serif;font-weight:800;font-size:40px;color:#777;letter-spacing:1px}
.header-phone{position:absolute;right:84px;top:36px;display:flex;align-items:center;gap:14px;font-family:"Exo 2",sans-serif;font-style:italic;font-weight:700;font-size:21px;color:#333}
.header-phone svg{width:26px;height:26px}
/* nav */
.main-nav{top:125px;height:56px;background:linear-gradient(var(--blue-light),var(--blue));display:flex;align-items:center;padding-left:98px}
.main-nav a{font-family:"Exo 2",sans-serif;font-style:italic;font-weight:800;font-size:19px;color:var(--white);text-decoration:none;text-transform:uppercase}
.main-nav a.active{color:#0f3f63}
.main-nav a:nth-child(1){width:126px}.main-nav a:nth-child(2){width:160px}.main-nav a:nth-child(3){width:160px}
.main-nav a:nth-child(4){width:150px}.main-nav a:nth-child(5){width:150px}.main-nav a:nth-child(6){width:150px}
/* hero */
.hero{top:181px;height:533px}
.hero-photo{position:absolute;inset:0;background:linear-gradient(100deg,#c9d3dc 0%,#e9edf1 35%,#aab6c2 60%,#2c3646 100%)}
.hero-caption{position:absolute;left:0;bottom:0;width:100%;height:56px;background:rgba(30,30,30,.85);text-align:center;font-family:"Exo 2",sans-serif;font-style:italic;font-weight:800;font-size:33px;line-height:56px;color:var(--white)}
.hero-caption span{color:var(--blue-light)}
/* welcome */
.welcome{top:714px;height:427px}
.welcome h1{position:absolute;left:83px;top:58px;width:650px;font-size:20px;white-space:nowrap;letter-spacing:.2px}
.welcome-text{position:absolute;left:83px;top:110px;width:620px;font-size:13.2px;line-height:23px;color:#222}
.welcome-text p{margin-bottom:8px}
.inquiry{position:absolute;left:765px;top:48px;width:356px;height:325px;background:#e3e3e3;border:1px solid #cfcfcf}
.inquiry-title{position:absolute;left:44px;top:-10px;width:268px;height:42px;background:linear-gradient(#8d8d8d,#5d5d5d);color:var(--white);font-family:"Exo 2",sans-serif;font-style:italic;font-weight:700;font-size:20px;text-align:center;line-height:42px}
.inquiry .field{position:absolute;left:20px;width:316px;height:36px;background:var(--white);border:1px solid #ccc;font-size:12px;color:#666;padding:10px 9px}
.inquiry .message{height:78px}
.inquiry .submit{position:absolute;left:26px;top:264px;width:124px;height:40px;background:var(--blue);border:2px solid #d0e7f7;color:var(--white);font-family:"Exo 2",sans-serif;font-weight:700;font-size:19px;text-align:center;line-height:36px}
/* services */
.services{top:1141px;height:405px;background:var(--grey-bg)}
.services h2{position:absolute;width:100%;top:44px;text-align:center;font-size:29px}
.section-rule{position:absolute;left:563px;width:74px;height:2px;background:var(--blue)}
.service-card{position:absolute;top:152px;width:316px;height:185px;background:var(--white);border-radius:12px;box-shadow:0 6px 8px rgba(0,0,0,.2);text-align:center}
.service-icon{position:absolute;left:123px;top:-32px;width:70px;height:70px;border-radius:4px;display:flex;align-items:center;justify-content:center}
.service-card h3{margin-top:72px;font-family:"Exo 2",sans-serif;font-style:italic;font-weight:700;font-size:15px;color:#555}
.service-card p{margin:22px auto 0;width:240px;font-size:12.5px;line-height:19px;color:#444}
.service-more{position:absolute;left:145px;bottom:-8px;width:26px;height:24px;color:var(--white);font-size:18px;font-weight:700;line-height:24px}
/* testimonials */
.testimonials{top:1546px;height:363px}
.testimonials h2{position:absolute;width:100%;top:54px;text-align:center;font-size:29px}
.quote{position:absolute;left:200px;top:148px;width:800px;text-align:center;font-style:italic;font-size:14.5px;line-height:29px;color:#333}
.quote-mark{font-family:"Tinos",serif;font-size:38px;color:#aaa;line-height:0;vertical-align:-10px}
.quote-author{position:absolute;width:100%;top:266px;text-align:center;font-size:16px;font-weight:700;color:#222}
.quote-author small{display:block;font-size:14px;margin-top:6px}
.slider-arrow{position:absolute;top:198px;width:30px;height:60px}
/* feature panels */
.features{top:1909px;height:387px}
.feature{position:absolute;top:0;height:387px;color:var(--white)}
.feature-support{left:0;width:604px;background:linear-gradient(var(--blue-light),var(--blue-dark));clip-path:polygon(0 0,578px 0,604px 30px,604px 387px,0 387px)}
.feature-outsourcing{left:604px;width:596px;background:linear-gradient(#e2e2e2,var(--grey-panel) 60%,#6f6f6f);clip-path:polygon(0 30px,26px 0,596px 0,596px 387px,0 387px)}
.feature h2{position:absolute;top:62px;display:flex;align-items:center;gap:12px;font-family:"Exo 2",sans-serif;font-style:italic;font-weight:800;font-size:23px;text-transform:uppercase;white-space:nowrap}
.feature-outsourcing h2{color:#1f1f1f}
.feature-photo{position:absolute;top:128px;width:204px;height:185px;border:3px solid #ddd}
.feature p{position:absolute;top:124px;width:270px;font-size:13.2px;line-height:26px}
.read-more{position:absolute;top:278px;width:152px;height:38px;font-family:"Tinos",serif;font-size:17px;line-height:36px;text-align:center}
.feature-support .read-more{left:308px;background:linear-gradient(#aaa,#777);border:1px solid #ccc}
.feature-outsourcing .read-more{left:252px;background:var(--blue);border:2px solid #d0e7f7}
/* tagline */
.tagline{top:2296px;height:170px;text-align:center}
.tagline h2{margin-top:44px;font-size:39px;text-transform:none;font-weight:700;letter-spacing:.5px}
.tagline p{font-family:"Exo 2",sans-serif;font-style:italic;font-weight:700;font-size:26px;color:var(--ink);margin-top:6px}
/* footer */
.site-footer{top:2466px;height:325px;background:linear-gradient(#2b2f36,#3a3e45 60%,#22252a);color:#e8e8e8}
.footer-col{position:absolute;top:52px}
.footer-col h3{font-size:17px;font-weight:400;color:var(--white);padding-bottom:12px;border-bottom:1px solid #555;width:180px}
.footer-col h3 span{color:var(--blue-light)}
.quick-links{left:87px}
.quick-links ul{list-style:none;margin-top:14px}
.quick-links li{font-size:13px;line-height:25px;padding-left:18px;position:relative}
.quick-links li::before{content:"";position:absolute;left:0;top:11px;width:4px;height:4px;background:var(--blue-light)}
.contact-details{left:320px}
.contact-details p{font-size:13px;line-height:22px;margin-top:14px}
.contact-line{display:flex;align-items:center;gap:10px;font-size:13px;margin-top:14px}
.contact-line svg{width:14px;height:14px}
.get-social{left:646px}
.social-line{display:flex;align-items:center;gap:14px;font-size:13px;margin-top:16px}
.social-line i{display:block;width:28px;height:28px;background:#555;border:1px solid #777}
.footer-brand{position:absolute;left:868px;top:80px;display:flex;align-items:center;gap:12px}
.footer-brand .brand-mark{width:56px;height:56px}
.footer-brand .brand-name{color:var(--blue-light);font-size:24px}
.copyright{top:2791px;height:44px;background:var(--blue);color:var(--white);font-size:14px;text-align:center;line-height:44px}
</style>
</head>
<body>

<div class="section top-bar">
  <div class="social-top" aria-label="Social links"><i></i><i></i><i></i><i></i></div>
</div>

<header class="section site-header">
  <div class="brand"><div class="brand-mark"></div><div class="brand-name">KELVANBROOK</div></div>
  <div class="header-phone">
    <svg viewBox="0 0 26 26"><rect width="26" height="26" rx="3" fill="#1a8fd6"/><path d="M8 6l3 0 1 4-2 1.5c1 2.2 2.3 3.5 4.5 4.5L16 14l4 1v3c-7 0-12-5-12-12z" fill="#fff"/></svg>
    (555) 014-2280
  </div>
</header>

<nav class="section main-nav">
  <a class="active">Home</a><a>About Us</a><a>Services</a><a>Support</a><a>Clients</a><a>Careers</a><a>Contact Us</a>
</nav>

<section class="section hero">
  <div class="hero-photo" role="img" aria-label="Photo of a business team smiling in a bright office meeting"></div>
  <div class="hero-caption">Let Us Worry About Your Technology... <span>So You Don't Have To!</span></div>
</section>

<section class="section welcome">
  <h1 class="heading">Welcome to Kelvanbrook <span>Development Group, Inc</span></h1>
  <div class="welcome-text">
    <p>Kelvanbrook Development Group, Inc. was established in 1991. Our mission is helping businesses and individuals realize a Return on Investment by implementing today's advanced technologies. As a small business we understand the importance of technology and personalized attention. Every member of our support team has worked with both large and small companies supporting a multitude of applications, networks and environments.</p>
    <p>We interface daily with Clients and their customers to establish your support needs. A prerequisite for working with Kelvanbrook is having both the technological knowledge and the customer skills to communicate and work with customers to resolve technology issues. Whether it is a simple computer network, phone systems, or an advanced integrated infrastructure, we will study your requirements, suggest methodologies, and implement the design.</p>
  </div>
  <form class="inquiry">
    <div class="inquiry-title">Quick Inquiry</div>
    <div class="field" style="top:52px">First Name</div>
    <div class="field" style="top:94px">Email</div>
    <div class="field" style="top:136px">Phone</div>
    <div class="field message" style="top:178px">Message</div>
    <div class="submit">Submit</div>
  </form>
</section>

<section class="section services">
  <h2 class="heading">Our <span>Services</span></h2>
  <div class="section-rule" style="top:90px"></div>
  <div class="service-card" style="left:77px">
    <div class="service-icon" style="background:var(--blue)"><svg width="40" height="40" viewBox="0 0 40 40" fill="none" stroke="#fff" stroke-width="3"><path d="M20 4v32M4 20h32M8 8l24 24M32 8L8 32"/></svg></div>
    <h3>Managed IT Solutions</h3>
    <p>Duis autem vel eum iriure do in hendrerit in vulputate Duis autem he....</p>
    <div class="service-more" style="background:var(--blue)">+</div>
  </div>
  <div class="service-card" style="left:442px">
    <div class="service-icon" style="background:#777"><svg width="40" height="40" viewBox="0 0 40 40" fill="none" stroke="#fff" stroke-width="3"><circle cx="20" cy="17" r="9"/><path d="M8 34c2-6 7-8 12-8s10 2 12 8"/></svg></div>
    <h3>Remote Diagnostic &amp; Support</h3>
    <p>Duis autem vel eum iriure do in hendrerit in vulputate Duis autem he....</p>
    <div class="service-more" style="background:#888">+</div>
  </div>
  <div class="service-card" style="left:807px">
    <div class="service-icon" style="background:#777"><svg width="40" height="40" viewBox="0 0 40 40" fill="#fff"><rect x="4" y="14" width="32" height="20"/><rect x="9" y="8" width="6" height="6"/><rect x="25" y="8" width="6" height="6"/></svg></div>
    <h3>Infrastructure Design &amp; Installation</h3>
    <p>Duis autem vel eum iriure do in hendrerit in vulputate Duis autem he....</p>
    <div class="service-more" style="background:#888">+</div>
  </div>
</section>

<section class="section testimonials">
  <h2 class="heading">Clients <span>Testimonials</span></h2>
  <div class="section-rule" style="top:102px"></div>
  <svg class="slider-arrow" style="left:114px" viewBox="0 0 30 60"><path d="M26 4L4 30l22 26" fill="none" stroke="#999" stroke-width="2"/></svg>
  <p class="quote"><span class="quote-mark">&ldquo;</span> Lorem ipsum dolor sit amet, consectetuer adipiscing elit, sed diam nonummy nibh euismod tincidunt ut laoreet dolore magna aliquam erat volutpat. Ut wisi enim ad minim veniam, quis nostrud exercimori mornkle tation ullamcorper suscipit lobortis nisl ut aliquip ex ea commodo consequat. <span class="quote-mark">&rdquo;</span></p>
  <div class="quote-author">Dana R.<small>Alder Point, CA</small></div>
  <svg class="slider-arrow" style="left:1056px" viewBox="0 0 30 60"><path d="M4 4l22 26L4 56" fill="none" stroke="#999" stroke-width="2"/></svg>
</section>

<section class="section features">
  <div class="feature feature-support">
    <h2 style="left:78px"><svg width="30" height="32" viewBox="0 0 30 32" fill="#fff"><circle cx="15" cy="10" r="8"/><path d="M2 32c1-8 6-12 13-12s12 4 13 12z"/></svg>IT Support Solutions</h2>
    <div class="feature-photo" style="left:83px;background:linear-gradient(120deg,#2c3e58,#6d88a8 50%,#1d2634)" role="img" aria-label="Photo of technicians working at a server rack"></div>
    <p style="left:308px">Lorem ipsum dolor sit amet, consecretk etuer adipiscing elit, sed diam nonumre my nibh euismod tincidunt ut laoreet et re olore magna aliquam erat volutpt. Ut wisi minim consequat.</p>
    <div class="read-more">Read More &rarr;</div>
  </div>
  <div class="feature feature-outsourcing">
    <h2 style="left:34px"><svg width="34" height="30" viewBox="0 0 34 30" fill="#1f1f1f"><circle cx="17" cy="8" r="5"/><circle cx="5" cy="12" r="4"/><circle cx="29" cy="12" r="4"/><rect x="10" y="15" width="14" height="10"/><rect x="0" y="18" width="9" height="8"/><rect x="25" y="18" width="9" height="8"/></svg>Our Outscourcing Technology</h2>
    <div class="feature-photo" style="left:32px;background:radial-gradient(circle at 50% 40%,#9fd3f5,#2e6ea8 45%,#0d1b2c)" role="img" aria-label="Illustration of a glowing globe and digital screens above a hand"></div>
    <p style="left:252px">Lorem ipsum dolor sit amet, consecretk etuer adipiscing elit, sed diam nonumre my nibh euismod tincidunt ut laoreet et re olore magna aliquam erat volutpt. Ut wisi minim consequat.</p>
    <div class="read-more">Read More &rarr;</div>
  </div>
</section>

<section class="section tagline">
  <h2 class="heading">IT solutions that work for your business</h2>
  <p>A Full Service Technology Company</p>
</section>

<footer class="section site-footer" role="img" aria-label="Night city skyline behind the footer">
  <div class="footer-col quick-links">
    <h3>Quick <span>Links</span></h3>
    <ul><li>Home</li><li>About Us</li><li>Services</li><li>Support</li><li>Clients</li><li>Careers</li><li>Contact Us</li></ul>
  </div>
  <div class="footer-col contact-details">
    <h3>Contact <span>Details</span></h3>
    <p>Kelvanbrook Development Group, Inc.</p>
    <p>418 Marlow Ave.<br>Brenford, Texas 77990</p>
    <div class="contact-line"><svg viewBox="0 0 14 14"><path d="M2 1h3l1 3-2 1c1 2 2 3 4 4l1-2 3 1v3C6 11 2 7 2 1z" fill="#3aa6e6"/></svg>(555) 014-2280</div>
    <div class="contact-line"><svg viewBox="0 0 14 14"><rect x="2" y="5" width="10" height="7" fill="#3aa6e6"/><rect x="4" y="1" width="6" height="4" fill="#3aa6e6"/></svg>(555) 014-2280</div>
    <div class="contact-line"><svg viewBox="0 0 14 14"><rect x="1" y="3" width="12" height="8" fill="#3aa6e6"/><path d="M1 3l6 5 6-5" fill="none" stroke="#fff"/></svg>info@kelvanbrook.com</div>
  </div>
  <div class="footer-col get-social">
    <h3>Get <span>Social</span></h3>
    <div class="social-line"><i></i>Friendly</div>
    <div class="social-line"><i></i>Chirper</div>
    <div class="social-line"><i></i>Circles</div>
    <div class="social-line"><i></i>Linkwork</div>
  </div>
  <div class="footer-brand"><div class="brand-mark"></div><div class="brand-name">KELVANBROOK</div></div>
</footer>

<div class="section copyright">Copyright &copy; 2017 Kelvanbrook Development Group, Inc. All Rights Reserved.</div>

</body>
</html>
```